Plakat für Tanzschule
Zielgruppe
Wir sind eine Tanzschule
Hallo,
ich benötige ein professionelles Design für ein Schild im Format 2 Meter breit × 1 Meter hoch (Querformat), das von einem stark frequentierten Parkplatz aus gut sichtbar ist.
✅ Ziel:
Gestaltung eines aufmerksamkeitsstarken, eleganten und energiegeladenen Werbeschilds
Das Schild soll sofort zeigen, worum es geht (Tanzstile) und zum kostenlosen Schnuppern motivieren
Die Gestaltung soll hochwertig und grafisch modern wirken
Bild / Hintergrund:
Ich habe einen ersten Design-Vorschlag hochgeladen (Screenshot)
⚠️ Ursprünglich hatte ich vor, ein bereits ausgeschnittenes und bearbeitetes Bild zu liefern (z. B. Unreinheiten und Störungen im Bild zu glätten oder zu entfernt und Zähne etwas weißer). Das kann ich jetzt leider doch nicht nachreichen. Daher müsste doch die Bearbeitung des Bildes mit übernommen werden.
✏️ Textinhalte (hierarchisch sortiert):
TANZSCHULE
Salsa · Bachata · Kizomba · Zouk
Jetzt Gratis Schnuppern!
Ritmo del Faro (Markenname)
www.ritmo-del-faro.de
???? Wichtig:
Die wichtigsten Inhalte (Tanzarten & CTA) müssen sofort erfassbar sein
Design bitte auf Fernwirkung, klare Lesbarkeit und modernes visuelles Layout ausrichten
Text in sinnvollen Größenabstufungen und mit sauberer visueller Hierarchie
Unsere eigentliche Hauptfarbe ist #ad194f, bis jetzt habe ich aber noch keine schöne Möglichkeit gefunden, in das aktuelle Design einzuarbeiten.
????️ Endformat & Übergabe:
Bitte das fertige Layout als .afdesign Datei (Affinity Designer) liefern
Optional PSD, EPS

```html
<!DOCTYPE html>
<html lang="de">
<head>
<meta charset="utf-8">
<title>Ritmo del Faro – Plakat</title>
<link rel="stylesheet" href="https://fonts.googleapis.com/css2?family=Antonio:wght@600&family=Kaushan+Script&family=Parisienne&family=Poppins:wght@600&display=swap">
<style>
  :root {
    --brand: #ad194f;
    --brand-bright: #c81f5f;
    --brand-deep: #a5164a;
    --paper: #f4f1f2;
    --grey: #cfcfd1;
    --band: #c4c4c6;
    --stage: #e6e6e8;
    --white: #ffffff;
  }
  html, body {
    margin: 0;
    width: 1200px;
    height: 896px;
    overflow: hidden;
    background: var(--stage);
  }
  .poster {
    position: absolute;
    left: 40px;
    top: 168px;
    width: 1120px;
    height: 560px;
    overflow: hidden;
    background: linear-gradient(90deg, var(--paper) 0%, var(--grey) 40%, var(--grey) 100%);
  }
  .color-field {
    position: absolute;
    left: 420px;
    top: 0;
    right: 0;
    bottom: 84px;
    background: linear-gradient(90deg, rgba(200,31,95,0) 0%, rgba(200,31,95,0.45) 30%, var(--brand-bright) 55%, var(--brand-deep) 100%);
  }
  .photo {
    position: absolute;
    left: 380px;
    top: 30px;
    width: 600px;
    height: 446px;
    border-radius: 4px;
    background: radial-gradient(ellipse at 45% 45%, #d9b48f 0%, #b98c70 30%, #6f7a68 62%, rgba(165,22,74,0) 80%);
  }
  .brand {
    position: absolute;
    left: 42px;
    top: 96px;
    display: flex;
    align-items: center;
    gap: 10px;
    color: var(--brand);
    font-family: "Parisienne", cursive;
    font-size: 34px;
  }
  .brand-dot {
    width: 22px;
    height: 22px;
    border-radius: 50%;
    background: var(--brand);
  }
  .styles {
    position: absolute;
    left: 40px;
    top: 178px;
    margin: 0;
    color: var(--brand);
    font-family: "Antonio", sans-serif;
    font-weight: 600;
    font-size: 74px;
    line-height: 72px;
    letter-spacing: -1px;
    text-transform: uppercase;
  }
  .styles span { display: block; }
  .band {
    position: absolute;
    left: 0;
    right: 0;
    bottom: 0;
    height: 84px;
    background: var(--band);
  }
  .cta {
    position: absolute;
    left: 36px;
    bottom: 14px;
    margin: 0;
    color: var(--white);
    font-family: "Kaushan Script", cursive;
    font-size: 44px;
    line-height: 56px;
  }
  .web {
    position: absolute;
    right: 40px;
    bottom: 22px;
    display: flex;
    align-items: center;
    gap: 12px;
    color: var(--brand);
    font-family: "Poppins", sans-serif;
    font-weight: 600;
    font-size: 34px;
    line-height: 40px;
  }
  .web svg { width: 38px; height: 38px; }
</style>
</head>
<body>
  <main class="poster">
    <div class="color-field"></div>
    <div class="photo" role="img" aria-label="Foto: lachendes Tanzpaar, Frau mit fliegenden blonden Haaren im weißen Top, Mann im grünen T-Shirt, vor pinkem Hintergrund mit Tänzer-Silhouette"></div>

    <div class="brand">
      <span class="brand-dot"></span>
      <span class="brand-name">Ritmo del Faro</span>
    </div>

    <h1 class="styles">
      <span>Salsa</span>
      <span>Bachata</span>
      <span>Kizomba</span>
      <span>Zouk</span>
    </h1>

    <div class="band"></div>
    <p class="cta">Jetzt Gratis Schnuppern!</p>
    <div class="web">
      <svg viewBox="0 0 24 24" fill="none" stroke="currentColor" stroke-width="2" aria-hidden="true">
        <circle cx="12" cy="12" r="10"/>
        <ellipse cx="12" cy="12" rx="4.5" ry="10"/>
        <line x1="2" y1="12" x2="22" y2="12"/>
        <path d="M4 7h16M4 17h16"/>
      </svg>
      <span>www.ritmo-del-faro.de</span>
    </div>
  </main>
</body>
</html>
```